Weightloss company needs Business Card

We want a business card that is clean and professional, yet portrays that we are a friendly, innovative, and versatile program designed to fit the needs of our clients.
I would like there to be 2 sides, one side having an appointment card, and the other side containing the logo and business information. There can be decorations on both sides. The logo is attached.

Target Market(s)

Men and women 40-60

Industry/Entity Type

Business

Contact Information for Business Card

Font styles to use
Sans Serif

Requirements
Must have
• The logo, space for business information
Nice to have
• The colors in the logo
Should not have
• No pictures of people or food

```html
<!DOCTYPE html>
<html lang="en">
<head>
<meta charset="utf-8">
<title>Brightpath Wellness – Business Card</title>
<link rel="stylesheet" href="https://fonts.googleapis.com/css2?family=Open+Sans:wght@400;600;700&display=swap">
<style>
  :root {
    --brand-red: #e8173f;
    --ink: #1c1c1c;
    --ink-soft: #3a3a3a;
    --card: #ffffff;
    --backdrop: #ecebe8;
    --card-shadow: rgba(0, 0, 0, 0.18);
  }
  * { box-sizing: border-box; margin: 0; padding: 0; }
  html, body {
    width: 1200px; height: 900px; overflow: hidden;
    background: var(--backdrop);
    font-family: "Open Sans", Arial, sans-serif;
    color: var(--ink);
  }
  .sheet {
    width: 1200px; height: 900px;
    display: flex; align-items: center; justify-content: center; gap: 50px;
  }
  .card {
    position: relative;
    width: 540px; height: 309px;
    background: var(--card);
    box-shadow: 0 10px 28px var(--card-shadow);
  }
  /* Brand wordmark stand-in */
  .brand {
    position: absolute;
    display: flex; align-items: center; gap: 10px;
  }
  .brand-dot {
    width: 22px; height: 22px; border-radius: 50%;
    background: var(--brand-red);
  }
  .brand-name {
    font-weight: 700; font-size: 25px; color: var(--brand-red);
    letter-spacing: -0.2px; white-space: nowrap;
  }

  /* Appointment side */
  .appointment-heading {
    position: absolute; left: 232px; top: 30px;
    font-size: 14px; font-weight: 600; color: var(--brand-red);
    letter-spacing: 0.2px;
  }
  .appointment-fields { position: absolute; left: 232px; top: 62px; width: 280px; }
  .field {
    display: flex; align-items: flex-end; gap: 4px;
    height: 30px; font-size: 12.5px; font-weight: 600; color: var(--brand-red);
  }
  .field-line {
    flex: 1; border-bottom: 2px dotted var(--ink); margin-bottom: 4px;
  }
  .field-unit { color: var(--ink); font-size: 11px; font-weight: 600; }
  .appointment .brand { left: 28px; top: 186px; }
  .notice {
    position: absolute; left: 0; right: 0; bottom: 26px;
    text-align: center; font-size: 14.5px; font-weight: 700; color: var(--ink);
  }

  /* Contact side */
  .contact-block { position: absolute; left: 300px; top: 34px; }
  .person-name { font-size: 18px; font-weight: 600; color: var(--brand-red); line-height: 1.1; }
  .person-role { font-size: 12px; color: var(--ink-soft); margin-top: 2px; }
  .address { font-size: 12.5px; color: var(--ink-soft); line-height: 1.35; margin-top: 14px; }
  .contact-list { list-style: none; margin-top: 12px; }
  .contact-list li {
    display: flex; align-items: center; gap: 10px;
    font-size: 12.5px; color: var(--ink-soft); line-height: 1.45;
  }
  .contact-list svg { width: 10px; height: 10px; fill: var(--brand-red); flex: none; }
  .details .brand { left: 120px; top: 222px; }
  .details .brand-name { font-size: 30px; }
  .details .brand-dot { width: 26px; height: 26px; }
</style>
</head>
<body>
<main class="sheet">

  <section class="card appointment" aria-label="Appointment card">
    <h2 class="appointment-heading">YOUR NEXT APPOINTMENT IS</h2>
    <div class="appointment-fields">
      <div class="field"><span class="field-line"></span></div>
      <div class="field">Name: <span class="field-line"></span></div>
      <div class="field">Date: <span class="field-line"></span><span class="field-unit">PM</span></div>
      <div class="field">Time: <span class="field-line"></span><span class="field-unit">AM</span><span class="field-line"></span></div>
    </div>
    <div class="brand">
      <span class="brand-dot"></span>
      <span class="brand-name">Brightpath Wellness</span>
    </div>
    <p class="notice">If unable to keep appointment, kindly give 24hrs notice.</p>
  </section>

  <section class="card details" aria-label="Contact card">
    <div class="contact-block">
      <p class="person-name">Daniel Carver</p>
      <p class="person-role">Managing Director</p>
      <p class="address">12345, Address Goes Here<br>Country Name, 123456.</p>
      <ul class="contact-list">
        <li>
          <svg viewBox="0 0 10 10" aria-hidden="true"><path d="M2 0.5 L3.6 2.6 L2.8 3.6 Q4 6 6.4 7.2 L7.4 6.4 L9.5 8 L8.4 9.5 Q4.5 9.3 1.6 6.4 Q0.3 4.4 0.5 1.6 Z"/></svg>
          044-555 210 734
        </li>
        <li>
          <svg viewBox="0 0 10 10" aria-hidden="true"><path d="M0.5 2 H9.5 V8.5 H0.5 Z M0.5 2 L5 5.5 L9.5 2" stroke="#fff" stroke-width="0.9"/></svg>
          hello@brightpathwell.com
        </li>
        <li>
          <svg viewBox="0 0 10 10" aria-hidden="true"><path d="M4.2 5.8 L5.8 4.2" stroke="#e8173f" stroke-width="1.2"/><path d="M1.5 6.5 L3.5 4.5 L4.3 5.3 L2.8 6.8 L3.2 7.2 L4.7 5.7 L5.5 6.5 L3.5 8.5 Q2.5 9.5 1.5 8.5 Q0.5 7.5 1.5 6.5 Z M8.5 3.5 L6.5 5.5 L5.7 4.7 L7.2 3.2 L6.8 2.8 L5.3 4.3 L4.5 3.5 L6.5 1.5 Q7.5 0.5 8.5 1.5 Q9.5 2.5 8.5 3.5 Z"/></svg>
          www.brightpathwell.com
        </li>
      </ul>
    </div>
    <div class="brand">
      <span class="brand-dot"></span>
      <span class="brand-name">Brightpath Wellness</span>
    </div>
  </section>

</main>
</body>
</html>
```